Calvanto Group Real Estate Company business cards

New business card design, we are generally happy with the basic layout of the existing front of business card, (feel free to change) but require a head shot photo on the back side.

http://www.calvanto.com.au/

Attached logos, and existing business card

------------------------------

Target Market(s)

Real estate

Industry/Entity Type

Real Estate

Contact Information for Business Card

Standard size double sided

Font styles to use
Other font styles liked:
• Futura

Requirements
Must have
• Photo head shot on the back side
Nice to have
• yes
Should not have
• No

```html
<!DOCTYPE html>
<html lang="en">
<head>
<meta charset="utf-8">
<title>Calvanto Group business cards</title>
<link href="https://fonts.googleapis.com/css2?family=Open+Sans:wght@400;600&family=Roboto+Condensed:wght@700&display=swap" rel="stylesheet">
<style>
  :root {
    --purple: #2b1a63;
    --orange: #f28a1e;
    --ink: #3a3a3a;
    --paper: #f7f7f7;
    --stage: #4a4a4a;
  }
  * { margin: 0; padding: 0; box-sizing: border-box; }
  html, body { width: 1200px; height: 750px; overflow: hidden; }
  body {
    background: var(--stage);
    position: relative;
    font-family: "Open Sans", Arial, sans-serif;
    color: var(--ink);
  }
  .card { position: absolute; overflow: hidden; }

  /* Front */
  .card-front {
    left: 214px; top: 321px; width: 460px; height: 263px;
    background: var(--paper);
  }
  .brand {
    position: absolute; left: 248px; top: 32px; width: 180px;
    text-align: center;
  }
  .brand-name {
    font-size: 30px; font-weight: 600; color: var(--purple);
    letter-spacing: -0.5px; line-height: 1;
  }
  .tagline {
    font-family: "Roboto Condensed", Arial, sans-serif;
    font-weight: 700; font-size: 12px; color: var(--purple);
    margin-top: 14px; word-spacing: 4px;
  }
  .name-bar {
    position: absolute; left: 0; top: 140px; width: 9px; height: 34px;
    background: var(--purple);
  }
  .person-name {
    position: absolute; left: 23px; top: 136px;
    font-size: 18px; font-weight: 600; color: var(--purple);
  }
  .person-role {
    position: absolute; left: 23px; top: 159px;
    font-size: 13.5px; color: var(--orange);
  }
  .rule {
    position: absolute; left: 72px; top: 171px; width: 377px; height: 1px;
    background: var(--orange); opacity: 0.7;
  }
  .contacts { position: absolute; left: 25px; top: 184px; list-style: none; }
  .contacts li {
    display: flex; align-items: center; gap: 7px;
    font-size: 12.5px; height: 18px;
  }
  .contacts svg { width: 12px; height: 12px; fill: var(--purple); }
  .company {
    position: absolute; right: 24px; top: 204px; text-align: right;
    font-size: 13px; line-height: 17px;
  }
  .company strong { font-weight: 600; }
  .base-band { position: absolute; left: 0; bottom: 0; width: 460px; height: 10px; }

  /* Back */
  .card-back {
    left: 705px; top: 130px; width: 263px; height: 461px;
    background: var(--orange);
  }
  .headshot {
    width: 263px; height: 348px;
    background: linear-gradient(180deg, #2e1d6e 0%, #2a1a62 70%, #243056 100%);
  }
  .back-brand { text-align: center; padding-top: 22px; }
  .back-brand .brand-name { color: #231a1a; font-size: 32px; }
  .back-brand .tagline { color: var(--purple); margin-top: 16px; }
  .back-web {
    font-size: 12.5px; letter-spacing: 2.6px; color: #2a1a1a; margin-top: 8px;
  }
</style>
</head>
<body>

<section class="card card-front" aria-label="Business card front">
  <div class="brand">
    <div class="brand-name">Calvanto Group</div>
    <div class="tagline">Buy | Sell | Rent</div>
  </div>

  <div class="name-bar"></div>
  <h1 class="person-name">Daniel Tran</h1>
  <p class="person-role">Director</p>
  <div class="rule"></div>

  <ul class="contacts">
    <li>
      <svg viewBox="0 0 24 24"><path d="M6.6 10.8a15.1 15.1 0 0 0 6.6 6.6l2.2-2.2a1 1 0 0 1 1-.25 11.4 11.4 0 0 0 3.6.57 1 1 0 0 1 1 1V20a1 1 0 0 1-1 1A17 17 0 0 1 3 4a1 1 0 0 1 1-1h3.5a1 1 0 0 1 1 1c0 1.25.2 2.45.57 3.6a1 1 0 0 1-.25 1z"/></svg>
      0412 555 308
    </li>
    <li>
      <svg viewBox="0 0 24 24"><path d="M2 5h20v14H2z" fill="none"/><path d="M2 5h20v2l-10 6L2 7zM2 9l10 6 10-6v10H2z"/></svg>
      daniel.tran@calvanto.com.au
    </li>
    <li>
      <svg viewBox="0 0 24 24"><circle cx="12" cy="12" r="10"/><path d="M7 8c2 0 3 1 3 3s-2 2-2 4M14 5c0 2 2 2 3 3s-1 3 1 4M13 20c0-2 1-3 3-3" stroke="#f7f7f7" stroke-width="1.6" fill="none"/></svg>
      www.calvanto.com.au
    </li>
  </ul>

  <div class="company">
    <strong>Calvanto Group</strong><br>
    ABN: 41 205 618 937
  </div>

  <svg class="base-band" viewBox="0 0 460 10" preserveAspectRatio="none">
    <polygon points="0,0 302,0 298,10 0,10" fill="var(--purple)"/>
    <polygon points="303,0 305,0 301,10 299,10" fill="#ffffff"/>
    <polygon points="306,0 460,0 460,10 302,10" fill="var(--orange)"/>
  </svg>
</section>

<section class="card card-back" aria-label="Business card back">
  <div class="headshot" role="img" aria-label="Head-and-shoulders portrait of the director in a navy suit and blue tie on a deep purple background"></div>
  <div class="back-brand">
    <div class="brand-name">Calvanto Group</div>
    <div class="tagline">Buy | Sell | Rent</div>
    <div class="back-web">www.calvanto.com.au</div>
  </div>
</section>

</body>
</html>
```